Business cards to launch an education platform

Hi,
I am looking at having new business cards designed.
I am a startup, developing a web platform for schools and university, the education world. It's an online assessment system.
I would like a card that looks classy, and that is using the colors and the font of my logo.

I have attached:
1) my logo
2) A business card that I have designed quickly so you can have all the information required in the card, but I really don't like it.
3) The font that I am using (Lato Regular) to design my web platform
4) Some screenshots of my web platform so you can have a look at the style that I have.

Target Market(s)

Major market: Education system: Schools and university
Minor markets: Business in general

Industry/Entity Type

Business

Contact Information for Business Card

Clara Fenwick
Director

M: 0437 518 902
E: clara.fenwick@amberLoomSystems.com.au

Requirements
Must have
• The colors of my logo

```html
<!DOCTYPE html>
<html lang="en">
<head>
<meta charset="utf-8">
<title>Amber Loom Systems – Business Cards</title>
<link rel="stylesheet" href="https://fonts.googleapis.com/css2?family=Lato:wght@300;400;700&display=swap">
<style>
  :root {
    --backdrop: #e6e7e8;
    --card-white: #ffffff;
    --card-shade: #f1f2f3;
    --brand-blue: #1a7fd0;
    --brand-deep: #0f63b3;
    --brand-cyan: #2cc3ee;
    --brand-light: #7fdcf6;
    --ink-dark: #1d2a38;
    --ink-light: #ffffff;
  }
  * { box-sizing: border-box; margin: 0; padding: 0; }
  html, body {
    width: 1200px; height: 747px; overflow: hidden;
    background: var(--backdrop);
    font-family: "Lato", Arial, sans-serif;
  }
  .canvas {
    position: relative; width: 1200px; height: 747px;
  }
  .card {
    position: absolute; top: 230px;
    width: 500px; height: 286px;
    background: linear-gradient(135deg, var(--card-white) 55%, var(--card-shade));
    box-shadow: 0 10px 24px rgba(0,0,0,0.14);
    overflow: hidden;
  }
  .card--front { left: 70px; }
  .card--back { left: 630px; }

  .brand {
    display: flex; align-items: center; gap: 10px;
    color: var(--brand-blue); font-weight: 400;
  }
  .brand__mark {
    width: 22px; height: 22px; background: var(--brand-blue);
  }
  .card--front .brand {
    position: absolute; left: 50%; top: 50%;
    transform: translate(-50%, -50%);
    font-size: 22px; letter-spacing: 1px;
  }
  .card--back .brand {
    position: absolute; right: 26px; top: 26px;
    font-size: 17px; letter-spacing: 1px;
  }
  .card--back .brand__mark { width: 18px; height: 18px; }

  .panel { position: absolute; left: 0; top: 0; width: 500px; height: 286px; }

  .contact {
    position: absolute; left: 28px; top: 112px; width: 340px;
    color: var(--ink-light);
  }
  .contact__name {
    font-size: 19px; font-weight: 400; letter-spacing: 1.5px; text-transform: uppercase;
  }
  .contact__title {
    font-size: 9px; font-weight: 300; letter-spacing: 1.5px; text-transform: uppercase;
    margin-bottom: 12px; opacity: .9;
  }
  .contact__list { list-style: none; }
  .contact__item {
    display: flex; align-items: center; gap: 8px;
    font-size: 11px; font-weight: 300; letter-spacing: .4px; margin-bottom: 6px;
  }
  .contact__item svg { width: 12px; height: 12px; flex: none; fill: var(--ink-light); }
  .contact__address { font-size: 8px; opacity: .9; }
</style>
</head>
<body>
<main class="canvas">

  <section class="card card--front" aria-label="Business card front">
    <div class="brand"><span class="brand__mark"></span><span class="brand__name">Amber Loom Systems</span></div>
  </section>

  <section class="card card--back" aria-label="Business card back">
    <svg class="panel" viewBox="0 0 500 286" aria-hidden="true">
      <polygon points="0,84 326,84 388,146 388,286 0,286" fill="var(--brand-cyan)"/>
      <polygon points="0,96 318,96 374,152 374,286 0,286" fill="var(--brand-blue)"/>
      <polygon points="0,262 374,262 374,286 0,286" fill="var(--brand-deep)"/>
      <rect x="0" y="270" width="500" height="16" fill="var(--brand-light)"/>
    </svg>

    <div class="brand"><span class="brand__mark"></span><span class="brand__name">Amber Loom Systems</span></div>

    <div class="contact">
      <h1 class="contact__name">Clara Fenwick</h1>
      <p class="contact__title">General Manager</p>
      <ul class="contact__list">
        <li class="contact__item">
          <svg viewBox="0 0 24 24"><path d="M6.6 10.8a15 15 0 0 0 6.6 6.6l2.2-2.2a1 1 0 0 1 1-.25 11.4 11.4 0 0 0 3.6.57 1 1 0 0 1 1 1V20a1 1 0 0 1-1 1A17 17 0 0 1 3 4a1 1 0 0 1 1-1h3.5a1 1 0 0 1 1 1c0 1.25.2 2.45.57 3.57a1 1 0 0 1-.25 1z"/></svg>
          <span>0437 518 902</span>
        </li>
        <li class="contact__item">
          <svg viewBox="0 0 24 24"><path d="M2 5h20v14H2zm2 2v.5l8 5 8-5V7l-8 5z"/></svg>
          <span>clara.fenwick@amberLoomSystems.com.au</span>
        </li>
        <li class="contact__item">
          <svg viewBox="0 0 24 24"><path d="M12 2a10 10 0 1 0 0 20 10 10 0 0 0 0-20zm0 2c1.2 0 2.6 2.4 3 6H9c.4-3.6 1.8-6 3-6zm-3 8h6c-.2 3.8-1.7 8-3 8s-2.8-4.2-3-8z"/></svg>
          <span>www.amberloomsystems.com.au</span>
        </li>
        <li class="contact__item contact__address">
          <svg viewBox="0 0 24 24"><path d="M12 2a7 7 0 0 0-7 7c0 5 7 13 7 13s7-8 7-13a7 7 0 0 0-7-7zm0 9.5A2.5 2.5 0 1 1 12 6.5a2.5 2.5 0 0 1 0 5z"/></svg>
          <span>14 Orchard Lane, Suite 3, Northbridge</span>
        </li>
      </ul>
    </div>
  </section>

</main>
</body>
</html>
```